Design a cover that embodies the concept of healing by Walking Out of Shadows

Subtitle: How to use tapping, applied kinesiology, and Chinese medicine to heal your body, free your mind and live in peace.

Tapping (Emotional Freedom Technique) is a modern mix of psychology and Chinese medicine that helps people to release the emotions they have inside that are contributing to the depression and anxiety they feel. Applied kinesiology or muscle testing is a biofeedback tool which helps to extract information from the body that can help people to profoundly heal. It can be used to determine whether heavy metals, heavy chemicals, food sensitivities or pathogens are causing the body problems. It can also be used to determine which supplements can help someone heal. This tool also can be used to identify emotions and memories that are also causing someone problems. Lastly, Chinese medicine uses food therapy, herbal formulas, meditation, tai chi (meditative movement), cupping and other tools to help people to be free of depression. This book is written to be information but also details my own personal journey of how I was able to heal from 11 years of heavy depression through the use of these tools.

The heart of the book is about emotional release, emotional freedom and emotional healing. You can surrender, release or let go of emotions and feel better very quickly. This certainly was my experience.

I would like the front and back cover to each be 8.5" x 5.5". I still have to get an ISBN number for the back page as well. Here is the text that I would like on the back cover for now: Millions of people feel the pain, loneliness, and agony of anxiety and depression every day. Many turn to Western medicine in the hopes that a pill will ease the pain and make the problem go away. Oftentimes, this only makes matters worse and doesn’t address the root cause. No one should have to struggle like this when natural answers exist that can address the physical, energetic, emotional, or spiritual causes of anxiety and depression. For 11 long years, Dr. Mervin personally struggled with heavy depression until he discovered answers that helped him to completely heal. Walking Out of Shadows is a guide that will help you discover - The two root physical causes of depression and exactly what to do to start healing today - How the negative emotions we have stored within from trauma and bad experiences can drive depression - Tools from Chinese medicine, applied kinesiology, and tapping to help you free your mind and live in peace - An actionable plan to help you let go of the pain, suffering, and negative emotions from your past Whether you feel depressed and anxious or know someone who struggles with these issues, Walking Out of Shadows will transform how you think about depression and will give you the tools to heal so that you can be free and live in peace. Dr. Mervin Holloway is a board-certified acupuncture physician licensed in the state of Florida. He received his training at the Marlow Institute of Restorative Health. He also graduated with a master’s degree in counseling and psychology from Cedarbrook School of Ministry. His mission is to help people transform their health and improve the quality of their life naturally. He lives in Orlando, FL where he runs a holistic medical clinic called Brightpath Wellness Center. www.drmervinholloway.example Picturegram: drmervinholloway Friendbook: brightpathwellnesscenter

Target Market(s)

Those who suffer from depression and anxiety and want to heal naturally

Industry/Entity Type

Health And Wellness

Requirements
Must have
• My picture should be small and go on the back cover next to the information about me. The front cover would be all graphical. Thank you. On the front cover my name should be posted as "Dr. Mervin Holloway, AP, MA"

```html
<!DOCTYPE html>
<html lang="en">
<head>
<meta charset="utf-8">
<title>Walking Out of Shadows — Book Cover</title>
<link rel="stylesheet" href="https://fonts.googleapis.com/css2?family=Abril+Fatface&family=Cormorant+Garamond:wght@500&family=Alegreya+Sans:wght@400&family=PT+Sans+Narrow:wght@400;700&display=swap">
<style>
  :root {
    --backdrop: #c9d0d1;
    --cover-back: #9fb0b1;
    --spine: #3b3c3d;
    --spine-text: #c9cfcf;
    --ink: #262626;
    --accent: #d92b2b;
    --sky-top: #f3f4f4;
    --sea: #9cb1b6;
    --sand: #c9bcb0;
    --shadow-warm: #8f8780;
    --band: #c7c2bc;
    --white: #ffffff;
  }
  * { margin: 0; padding: 0; box-sizing: border-box; }
  html, body { width: 1200px; height: 800px; overflow: hidden; }
  body { background: var(--backdrop); position: relative; font-family: "PT Sans Narrow", sans-serif; }

  .front-cover {
    position: absolute; left: 110px; top: 50px; width: 453px; height: 700px;
    overflow: hidden; background: var(--sky-top);
    box-shadow: 0 10px 30px rgba(0,0,0,.25);
  }
  .front-cover__art {
    position: absolute; left: 0; top: 0; width: 100%; height: 100%;
    background: linear-gradient(180deg, var(--sky-top) 0%, #dfe4e5 6%, var(--sea) 22%, #b9c6c8 36%, #c3c0bc 52%, #a89c92 64%, var(--sand) 78%, var(--shadow-warm) 100%);
  }
  .front-cover__author {
    position: absolute; top: 14px; width: 100%; text-align: center;
    font-family: "Cormorant Garamond", serif; font-weight: 500; font-size: 25px; color: var(--ink);
  }
  .front-cover__title {
    position: absolute; top: 198px; width: 100%; text-align: center;
    font-family: "Abril Fatface", serif; color: var(--ink); line-height: 1;
    text-shadow: 0 1px 2px rgba(255,255,255,.5);
  }
  .front-cover__title .line-1 { display: block; font-size: 46px; }
  .front-cover__title .joiner { display: block; font-size: 15px; color: var(--accent); margin: 2px 0 0; }
  .front-cover__title .line-2 { display: block; font-size: 60px; }
  .front-cover__subtitle-band {
    position: absolute; left: 0; bottom: 0; width: 100%; height: 112px;
    background: linear-gradient(180deg, rgba(199,194,188,.85), var(--band));
    padding: 12px 16px 0;
  }
  .front-cover__subtitle {
    font-family: "Alegreya Sans", sans-serif; font-size: 20px; line-height: 1.18;
    color: var(--ink); text-align: center;
  }

  .back-cover {
    position: absolute; left: 590px; top: 50px; width: 453px; height: 700px;
    background: var(--cover-back); overflow: hidden; padding: 22px 22px 0;
    box-shadow: 0 10px 30px rgba(0,0,0,.2);
  }
  .back-cover__motif {
    position: absolute; left: 150px; top: 60px; width: 230px; height: 560px;
    background: radial-gradient(ellipse at center, rgba(120,140,140,.22), rgba(120,140,140,0) 70%);
  }
  .back-cover__title {
    position: relative; font-family: "Abril Fatface", serif; font-size: 34px;
    color: var(--ink); text-align: center; white-space: nowrap;
  }
  .back-cover__title .joiner { font-size: 13px; color: var(--accent); }
  .back-cover__body {
    position: relative; margin-top: 12px; font-size: 10.4px; line-height: 1.4;
    color: var(--ink); text-align: justify;
  }
  .back-cover__body p { margin-bottom: 10px; }
  .back-cover__body strong { font-weight: 700; }
  .benefits { list-style: none; margin-bottom: 10px; }
  .benefits li { position: relative; padding-left: 7px; }
  .benefits li::before {
    content: ""; position: absolute; left: 0; top: 5px; width: 4px; height: 4px;
    border-radius: 50%; background: var(--accent);
  }
  .about-author { position: relative; display: flex; gap: 12px; margin-top: 8px; padding-left: 4px; }
  .about-author__photo {
    flex: 0 0 86px; height: 94px;
    background: linear-gradient(160deg, #7e9a6b, #c9b79a 55%, #e4dccb);
  }
  .about-author__bio { font-size: 10.2px; line-height: 1.4; text-align: justify; color: var(--ink); }
  .about-author__bio .name { color: var(--accent); font-weight: 700; }
  .contact {
    position: absolute; left: 26px; bottom: 48px; font-weight: 700; font-size: 10.5px;
    line-height: 1.55; color: var(--ink);
  }
  .isbn-box {
    position: absolute; right: 62px; bottom: 38px; width: 92px; height: 52px; background: var(--white);
  }

  .spine {
    position: absolute; left: 1043px; top: 50px; width: 46px; height: 700px;
    background: var(--spine); color: var(--spine-text);
    display: flex; flex-direction: column; align-items: center; justify-content: space-between;
    padding: 22px 0;
    box-shadow: 0 10px 30px rgba(0,0,0,.2);
  }
  .spine__title, .spine__author { writing-mode: vertical-rl; white-space: nowrap; }
  .spine__title { font-family: "Abril Fatface", serif; font-size: 22px; }
  .spine__title .joiner { font-size: 12px; color: var(--accent); }
  .spine__author { font-family: "Cormorant Garamond", serif; font-weight: 500; font-size: 20px; }
</style>
</head>
<body>

<section class="front-cover">
  <div class="front-cover__art" role="img" aria-label="Photographic collage: a woman in white with arms open on a beach with butterflies, two reaching hands with a glowing acupressure point, and a figure hunched in sorrow dissolving into dust below, with faint brush characters"></div>
  <p class="front-cover__author">Dr. Mervin Holloway, AP, MA</p>
  <h1 class="front-cover__title">
    <span class="line-1">Walking Out</span>
    <span class="joiner">of</span>
    <span class="line-2">Shadows</span>
  </h1>
  <div class="front-cover__subtitle-band">
    <p class="front-cover__subtitle">How to use tapping, applied kinesiology, and Chinese medicine to heal your body, free your mind and live in peace.</p>
  </div>
</section>

<section class="back-cover">
  <div class="back-cover__motif" role="img" aria-label="Faint large brush character for qi as background decoration"></div>
  <h2 class="back-cover__title">Walking Out <span class="joiner">of</span> Shadows</h2>
  <div class="back-cover__body">
    <p>Millions of people feel the pain, loneliness, and agony of anxiety and depression every day. Many turn to Western medicine in the hopes that a pill will ease the pain and make the problem go away. Oftentimes, this only makes matters worse and doesn’t address the root cause. No one should have to struggle like this when natural answers exist that can address the physical, energetic, emotional, or spiritual causes of anxiety and depression.</p>
    <p>For 11 long years, <strong>Dr. Mervin</strong> personally struggled with heavy depression until he discovered answers that helped him to completely heal. <strong>Walking Out of Shadows</strong> is a guide that will help you discover:</p>
    <ul class="benefits">
      <li>The two root physical causes of depression and exactly what to do to start healing today</li>
      <li>How the negative emotions we have stored within from trauma and bad experiences can drive depression</li>
      <li>Tools from Chinese medicine, applied kinesiology, and tapping to help you free your mind and live in peace</li>
      <li>An actionable plan to help you let go of the pain, suffering, and negative emotions from your past.</li>
    </ul>
    <p>Whether you feel depressed and anxious or know someone who struggles with these issues, <strong>Walking Out of Shadows</strong> will transform how you think about depression and will give you the tools to heal so that you can be free and live in peace.</p>
  </div>
  <div class="about-author">
    <div class="about-author__photo" role="img" aria-label="Small portrait photo of the author outdoors"></div>
    <p class="about-author__bio"><span class="name">Dr. Mervin Holloway</span> is a board-certified acupuncture physician licensed in the state of Florida. He received his training at the Marlow Institute of Restorative Health. He also graduated with a master’s degree in counseling and psychology from Cedarbrook School of Ministry. His mission is to help people transform their health and improve the quality of their life naturally. He lives in Orlando, FL where he runs a holistic medical clinic called Brightpath Wellness Center.</p>
  </div>
  <div class="contact">
    <p>www.drmervinholloway.example</p>
    <p>Picturegram: drmervinholloway</p>
    <p>Friendbook: brightpathwellnesscenter</p>
  </div>
  <div class="isbn-box" aria-label="Space reserved for ISBN"></div>
</section>

<aside class="spine">
  <span class="spine__title">Walking Out <span class="joiner">of</span> Shadows</span>
  <span class="spine__author">Dr. Mervin Holloway, AP, MA</span>
</aside>

</body>
</html>
```